One of Australia's fastest growing energy maintenance contractors needs a new website

www.brightleaf.com.au
Our business has evolved over the past years and now our website is no longer relevant.
We clean solar panels and we vacuum roof gutters.
We clean solar panels on the roofs of residential houses right up to billion dollar solar farms with in excess of 1 million panels. We offer thermal image testing and bird proofing for our residential and commercial clients and thermal drone imaging services for our solar farm clients.
We vacuum clean roof gutters (using a LoftSuck) on the residential house next door right up to enormous private and public schools, colleges, shopping centres, strat complexes and commercial buildings.
When first built our business had more of a domestic residential skew and the website reflected that. While that is still part of our core business we are now bidding on and have secured large government, commercial and infrastructure contracts and our new website needs to reflect our growth and our new business. We need a new site that it optimised for both desktop ad phone viewing as our latest figures showed that 73% of people visiting our site are on mobile phones. We have an extensive amount of data on Tallymark Insights available as well as Bidlines. Both that would also need integrating with the site along with a few other plugins such as Quilro Chat IQ, Chatterbox etc along with SEO key words etc. We are also the winner and finalists over multiple years of the small business of the year awards and we like to proudly and prominently display those on our site.
We are looking for a new site with a modern professional feel / theme
There is a definitive break in our business between the solar Panel cleaning clients and the gutter cleaning clients so we would like a home page that begins with a simple choice:
Solar Panel Cleaning – Gutter Cleaning
With a professional full screen background image (we have hundreds to choose from) and along the bottom a small area with rights reserved etc, phone number etc (at some point in the future we will split these into two businesses but for now it’s what we have).
After that selection is made we would like a repeat of that same scenario but the selection is:
If it’s Solar Panel Cleaning
(new background image)
Government – Infrastructure – Commercial – Residential
If it’s Gutter Cleaning
(new background image)
Government – Strata – Commercial – Residential
After making those choices then onto the relevant pages with background images relevant to each sector and a them that suits (on the residential we would like to keep the link to our tallymark reviews) - We will provide copy / text for each relevant page.
Other than that, a menu inclusive of the above and:
Resellers Portal – we will provide a link to this from Quilro CRM)
Customer portal (we will supply a link to this from our booking system)
We also need a page for our Solar Resellers / Partners page but we will give them a link to this, it won’t be listed on the site.
Request a quote page (Again we will provide information from Quilro as this will be linked to the CRM)
Standard contact us page inclusive of phone numbers, address and fields supplied from CRM
Sydney – 02 7391 8056
Southern Highlands – 02 4863 1708
Goulburn – 02 4863 1708
Canberra – 02 6172 4385
Wollongong – 02 4239 5817
sales@brightleaf.com.au
Head Office - Kelvin Ridge NSW 2590
ABN: 48093716552
Responsive Design: Optimized for desktop and mobile (73% mobile visitors).
Fast Loading Speed: Optimized for performance.
Smooth Transition Animations: For service and category selection.
Sticky Contact Bar: Always accessible at the bottom of mobile screens for quick calls.
SEO Optimization: Focused on government tenders, large-scale commercial contracts, and infrastructure projects.
Integrations
Tallymark Insights & Tallymark Bidlines.
Quilro Chat IQ.
Chatterbox Beacon.
SEO tools and keyword optimization.
Many many more images available if needed
Target Market(s)
Residential, commercial, Government

```html
<!DOCTYPE html>
<html lang="en">
<head>
<meta charset="utf-8">
<title>Brightleaf – Premier Solar Panel Cleaning</title>
<link href="https://fonts.googleapis.com/css2?family=Jost:wght@300;400;500;600&display=swap" rel="stylesheet">
<style>
:root{
  --brand:#1a5fa8;
  --sky:#22b0e7;
  --ink:#111418;
  --muted:#555b63;
  --line:#d9dde2;
  --soft:#f6f6f6;
  --white:#ffffff;
  --black:#000000;
  --star:#f5b301;
  --review-blue:#3d7ff0;
}
*{box-sizing:border-box;margin:0;padding:0}
html,body{width:1200px;height:3041px;overflow:hidden}
body{position:relative;font-family:"Jost",sans-serif;color:var(--ink);background:var(--white)}
.abs{position:absolute}
.btn{position:absolute;display:flex;align-items:center;justify-content:center;gap:8px;height:37px;border:1px solid var(--brand);border-radius:20px;color:var(--brand);font-size:10px;font-weight:500;text-decoration:none}
.btn svg{width:14px;height:6px}
.btn.light{border-color:var(--white);color:var(--white)}

.site-header{position:absolute;top:0;left:0;width:1200px;height:62px;background:var(--white);z-index:3}
.logo-badge{position:absolute;left:105px;top:0;width:142px;height:127px;z-index:4}
.logo-name{position:absolute;left:105px;top:60px;width:142px;text-align:center;font-size:16px;font-weight:500;color:var(--brand);z-index:5}
.main-nav{position:absolute;top:24px;font-size:10px;color:var(--ink)}
.main-nav a{position:absolute;white-space:nowrap;color:inherit;text-decoration:none}

.hero{position:absolute;top:62px;left:0;width:1200px;height:531px;background:linear-gradient(115deg,#2b3a52 0%,#4a5d78 35%,#6f7f5a 65%,#8a9a64 100%)}
.hero-title{position:absolute;top:245px;width:1200px;text-align:center;font-size:53px;font-weight:400;color:var(--white);letter-spacing:.5px}
.hero-sub{position:absolute;top:327px;width:1200px;text-align:center;font-size:23px;font-weight:300;line-height:33px;color:var(--white)}

.section-title{position:absolute;width:1200px;text-align:center;font-size:38px;font-weight:400;color:var(--ink)}

.review-bar{position:absolute;left:207px;top:754px;width:786px;height:43px;background:var(--white);box-shadow:0 1px 4px rgba(0,0,0,.15);border-radius:3px;display:flex;align-items:center;padding:0 15px;gap:8px;font-size:11px;font-weight:600}
.review-brand{font-size:16px;font-weight:500;color:var(--review-blue);margin-right:4px}
.stars{color:var(--star);letter-spacing:1px;font-size:13px}
.write-review{margin-left:auto;background:var(--review-blue);color:var(--white);font-size:10px;padding:6px 13px;border-radius:3px}
.review-card{position:absolute;top:809px;width:255px;height:168px;background:var(--white);box-shadow:0 1px 4px rgba(0,0,0,.15);border-radius:3px;padding:15px}
.review-head{display:flex;align-items:center;gap:10px}
.avatar{width:27px;height:27px;border-radius:50%;background:#7d8892;color:var(--white);font-size:14px;display:flex;align-items:center;justify-content:center}
.reviewer{font-size:11px;font-weight:600}
.review-date{font-size:8.5px;color:#8a9099;font-weight:400}
.source-dot{margin-left:auto;width:11px;height:11px;border-radius:50%;background:#c9ced4}
.review-card .stars{margin-top:7px;display:block}
.review-text{margin-top:6px;font-size:10px;line-height:15.5px;color:#2a2e33;height:62px;overflow:hidden}
.read-more{font-size:9.5px;color:#9aa0a7;margin-top:3px}

.why{position:absolute;top:1123px;left:0;width:1200px;height:429px;background:var(--soft)}
.feature{position:absolute;top:1283px;width:206px;text-align:center}
.feature svg{width:44px;height:44px;display:block;margin:0 auto}
.feature-name{margin-top:16px;font-size:13.5px}
.feature-text{margin-top:6px;font-size:9.5px;line-height:15px;color:var(--muted)}
.divider{position:absolute;top:1283px;width:1px;height:124px;background:var(--line)}

.accordion{position:absolute;left:262px;top:1710px;width:676px;border-top:1px solid var(--line)}
.acc-row{height:49px;border-bottom:1px solid var(--line);display:flex;align-items:center;justify-content:space-between;padding:0 25px;font-size:22px;font-weight:400}
.acc-row svg{width:22px;height:8px}
.acc-open{height:271px;background:#f4f4f4;border-bottom:1px solid var(--line);position:relative;padding:0 25px}
.acc-open-title{display:flex;justify-content:space-between;align-items:center;height:50px;font-size:22px;font-weight:500;color:var(--brand)}
.acc-open-title svg{width:22px;height:8px}
.acc-text{position:absolute;left:25px;top:92px;width:300px;font-size:9px;line-height:15px;color:#3a3f45}
.acc-photo{position:absolute;left:400px;top:65px;width:250px;height:187px;background:linear-gradient(160deg,#8fb3d1 0%,#c9a54a 45%,#4d6e8f 75%,#2e4a66 100%)}

.band{position:absolute;top:2346px;left:0;width:1200px;height:313px;background:var(--sky);overflow:hidden}
.band-photo{position:absolute;left:620px;top:0;width:580px;height:313px;clip-path:polygon(98px 0,580px 0,580px 313px,0 313px);background:linear-gradient(170deg,#c8def2 0%,#9cc2e4 25%,#d36d52 50%,#2c3f66 70%,#3e6a3a 100%)}
.band-title{position:absolute;left:107px;top:70px;font-size:40px;font-weight:400;line-height:54px;color:var(--white)}

.site-footer{position:absolute;top:2659px;left:0;width:1200px;height:382px;background:var(--black);color:var(--white)}
.footer-name{position:absolute;left:198px;top:190px;font-size:33px;font-weight:500}
.footer-mark{position:absolute;left:260px;top:80px;width:64px;height:64px;border-radius:50%;background:var(--sky)}
.col-title{position:absolute;top:77px;font-size:13px;display:flex;align-items:center;gap:16px}
.col-title span{display:block;width:100px;height:1px;background:#888}
.contact-list{position:absolute;left:469px;top:110px;list-style:none}
.contact-list li{height:25px;font-size:9px;display:flex;align-items:center;gap:9px}
.contact-list b{font-weight:600}
.contact-list svg{width:9px;height:9px}
.quick-links{position:absolute;left:731px;top:112px;list-style:none}
.quick-links li{height:25px;font-size:10px}
.social{position:absolute;left:969px;width:30px;height:30px;border-radius:50%;background:#3a3a3a}
.footer-bottom{position:absolute;top:320px;font-size:9px}
</style>
</head>
<body>

<header class="site-header">
  <nav class="main-nav">
    <a href="#" style="left:675px">Resellers Portal</a>
    <a href="#" style="left:775px">Customer portal</a>
    <a href="#" style="left:877px">Contact us</a>
  </nav>
  <a class="btn" href="#" style="left:956px;top:12px;width:138px">Request a Quote
    <svg viewBox="0 0 14 6"><path d="M0 3h13M10 .5 13 3l-3 2.5" fill="none" stroke="currentColor"/></svg></a>
</header>
<svg class="logo-badge" viewBox="0 0 142 127" aria-hidden="true"><path d="M0 0h142v62L78 124q-7 5-14 0L0 62z" fill="#fff"/></svg>
<div class="logo-name">Brightleaf</div>

<section class="hero" role="img" aria-label="Technician in hard hat cleaning a row of solar panels with a long brush"></section>
<h1 class="hero-title">Premier Solar Panel Cleaning</h1>
<p class="hero-sub">We have a detailed knowledge of the cleaning &amp; testing<br>of Solar Panels</p>
<a class="btn light" href="#" style="left:531px;top:425px;width:138px">Request a Quote
  <svg viewBox="0 0 14 6"><path d="M0 3h13M10 .5 13 3l-3 2.5" fill="none" stroke="currentColor"/></svg></a>

<h2 class="section-title" style="top:668px">We Love Happy Customers</h2>
<div class="review-bar">
  <span class="review-brand">Tallymark</span>
  <span>Excellent</span><span class="stars">★★★★★</span><span>4.9 &nbsp;|&nbsp; 392 reviews</span>
  <span class="write-review">Write a review</span>
</div>

<article class="review-card" style="left:207px">
  <div class="review-head"><div class="avatar">T</div><div><div class="reviewer">Tessa Marlowe</div><div class="review-date">16 January 2025</div></div><div class="source-dot"></div></div>
  <span class="stars">★★★★★</span>
  <p class="review-text">Brightleaf came on time. I was really well informed of any delay. The report is great and the feedback on our gutters and solar panels is full of detail. The before...</p>
  <p class="read-more">Read more</p>
</article>
<article class="review-card" style="left:472px">
  <div class="review-head"><div class="avatar" style="background:#1d3f78"></div><div><div class="reviewer">Corvane Health</div><div class="review-date">8 January 2025</div></div><div class="source-dot"></div></div>
  <span class="stars">★★★★★</span>
  <p class="review-text">Fantastic service all round.<br>Easy to set up the job and get a quote.<br>The quoted price was reasonable.<br>The person who came to do the work was...</p>
  <p class="read-more">Read more</p>
</article>
<article class="review-card" style="left:738px">
  <div class="review-head"><div class="avatar" style="background:#b9a99c"></div><div><div class="reviewer">Rolf DENHAM</div><div class="review-date">20 December 2024</div></div><div class="source-dot"></div></div>
  <span class="stars">★★★★★</span>
  <p class="review-text">Another great job Brightleaf do a great job and we use their services at least once a year and will continue. Their reports and photos are proof of a professional...</p>
  <p class="read-more">Read more</p>
</article>
<a class="btn" href="#" style="left:531px;top:1011px;width:138px">View all Review
  <svg viewBox="0 0 14 6"><path d="M0 3h13M10 .5 13 3l-3 2.5" fill="none" stroke="currentColor"/></svg></a>

<section class="why"></section>
<h2 class="section-title" style="top:1198px">Why Clean Your Panels?</h2>
<div class="feature" style="left:188px">
  <svg viewBox="0 0 44 44" fill="none" stroke="#1a5fa8" stroke-width="1.6"><circle cx="13" cy="13" r="9"/><path d="M13 8v5l3 2"/><path d="M20 40V28h5v12M28 40V20h5v20M36 40V24h5v16M4 40h38"/></svg>
  <p class="feature-name">Increased Efficiency</p>
  <p class="feature-text">Maintain and increase<br>the efficiency of your panels</p>
</div>
<div class="divider" style="left:394px"></div>
<div class="feature" style="left:394px">
  <svg viewBox="0 0 44 44" fill="none" stroke="#1a5fa8" stroke-width="1.6"><circle cx="22" cy="20" r="14"/><circle cx="22" cy="20" r="8"/><path d="M22 16l1.3 2.8 3 .3-2.2 2 .7 3-2.8-1.6-2.8 1.6.7-3-2.2-2 3-.3z"/><path d="M16 33l-2 9 8-4 8 4-2-9"/></svg>
  <p class="feature-name">Maintain Warranty</p>
  <p class="feature-text">Maintain warranty obligations</p>
</div>
<div class="divider" style="left:600px"></div>
<div class="feature" style="left:600px">
  <svg viewBox="0 0 44 44" fill="none" stroke="#1a5fa8" stroke-width="1.6"><circle cx="22" cy="20" r="13"/><circle cx="22" cy="20" r="2.5"/><path d="M22 17.5c-1-4 0-7 3-8M24 21c4 1 6 3 5 7M20 21c-3 3-6 3-8 1"/><path d="M22 33v9M22 2v4M6 20H2M42 20h-4"/></svg>
  <p class="feature-name">Increase Power Output</p>
  <p class="feature-text">Increase energy output by<br>20% or more</p>
</div>
<div class="divider" style="left:807px"></div>
<div class="feature" style="left:807px">
  <svg viewBox="0 0 44 44" fill="none" stroke="#1a5fa8" stroke-width="1.6"><path d="M22 3l16 6v12c0 10-7 17-16 20C13 38 6 31 6 21V9z"/><circle cx="22" cy="21" r="6"/><path d="M22 11v4M22 27v4M12 21h4M28 21h4M15 14l3 3M26 25l3 3M29 14l-3 3M18 25l-3 3"/></svg>
  <p class="feature-name">No Contact Covid Safe</p>
  <p class="feature-text">We use a contactless and covid<br>safe system</p>
</div>
<a class="btn" href="#" style="left:531px;top:1439px;width:138px">Request a Quote
  <svg viewBox="0 0 14 6"><path d="M0 3h13M10 .5 13 3l-3 2.5" fill="none" stroke="currentColor"/></svg></a>

<h2 class="section-title" style="top:1627px">Explore Solar Panel Cleaning</h2>
<div class="accordion">
  <div class="acc-row">About panel soiling<svg viewBox="0 0 22 8"><path d="M2 2l9 5 9-5" fill="none" stroke="#22b0e7" stroke-width="2.4"/></svg></div>
  <div class="acc-open">
    <div class="acc-open-title">Rain washes my panels<svg viewBox="0 0 22 8"><path d="M2 6l9-5 9 5" fill="none" stroke="#22b0e7" stroke-width="2.4"/></svg></div>
    <p class="acc-text">Answer this; does rain wash your car? even in milder climactic conditions with more rainy weather, it is noticeable that dirt will remain on the panels. this is true even when modules are installed at a steep incline, which helps to flush off water and dirt. moreover, dust tends to accumulate over time, and will</p>
    <a class="btn" href="#" style="left:25px;top:190px;width:112px">Learn More
      <svg viewBox="0 0 14 6"><path d="M0 3h13M10 .5 13 3l-3 2.5" fill="none" stroke="currentColor"/></svg></a>
    <div class="acc-photo" role="img" aria-label="Worker in yellow protective suit pressure washing solar panels"></div>
  </div>
  <div class="acc-row">Management plan<svg viewBox="0 0 22 8"><path d="M2 2l9 5 9-5" fill="none" stroke="#22b0e7" stroke-width="2.4"/></svg></div>
  <div class="acc-row">Beyond dust<svg viewBox="0 0 22 8"><path d="M2 2l9 5 9-5" fill="none" stroke="#22b0e7" stroke-width="2.4"/></svg></div>
  <div class="acc-row">Power loss<svg viewBox="0 0 22 8"><path d="M2 2l9 5 9-5" fill="none" stroke="#22b0e7" stroke-width="2.4"/></svg></div>
  <div class="acc-row">Do they really need cleaning?<svg viewBox="0 0 22 8"><path d="M2 2l9 5 9-5" fill="none" stroke="#22b0e7" stroke-width="2.4"/></svg></div>
</div>
<a class="btn" href="#" style="left:531px;top:2260px;width:138px">Request a Quote
  <svg viewBox="0 0 14 6"><path d="M0 3h13M10 .5 13 3l-3 2.5" fill="none" stroke="currentColor"/></svg></a>

<section class="band">
  <div class="band-photo" role="img" aria-label="House with red tiled roof covered in solar panels under a blue sky"></div>
  <h2 class="band-title">We use only the best ionic and<br>LoftSuck cleaning systems</h2>
  <a class="btn light" href="#" style="left:107px;top:207px;width:138px">Request a Quote
    <svg viewBox="0 0 14 6"><path d="M0 3h13M10 .5 13 3l-3 2.5" fill="none" stroke="currentColor"/></svg></a>
</section>

<footer class="site-footer">
  <div class="footer-mark"></div>
  <div class="footer-name">Brightleaf</div>

  <div class="col-title" style="left:469px">Contact us<span></span></div>
  <ul class="contact-list">
    <li><svg viewBox="0 0 10 10"><path d="M5 10S1 6 1 4a4 4 0 0 1 8 0c0 2-4 6-4 6z" fill="#22b0e7"/></svg><span><b>Head Office</b> - Kelvin Ridge NSW 2590</span></li>
    <li><svg viewBox="0 0 10 10"><rect x="1" y="2" width="8" height="6" fill="#22b0e7"/></svg>sales@brightleaf.com.au</li>
    <li><svg viewBox="0 0 10 10"><path d="M2 1l2 2-1 1.5q1 2 2.5 2.5L7 6l2 2-1.5 1.5Q3 8.5.5 2.5z" fill="#22b0e7"/></svg><span><b>Sydney</b> - 02 7391 8056</span></li>
    <li><svg viewBox="0 0 10 10"><path d="M2 1l2 2-1 1.5q1 2 2.5 2.5L7 6l2 2-1.5 1.5Q3 8.5.5 2.5z" fill="#22b0e7"/></svg><span><b>Southern Highlands</b>- 02 4863 1708</span></li>
    <li><svg viewBox="0 0 10 10"><path d="M2 1l2 2-1 1.5q1 2 2.5 2.5L7 6l2 2-1.5 1.5Q3 8.5.5 2.5z" fill="#22b0e7"/></svg><span><b>Goulburn</b> - 02 4863 1708</span></li>
    <li><svg viewBox="0 0 10 10"><path d="M2 1l2 2-1 1.5q1 2 2.5 2.5L7 6l2 2-1.5 1.5Q3 8.5.5 2.5z" fill="#22b0e7"/></svg><span><b>Canberra</b> - 02 6172 4385</span></li>
    <li><svg viewBox="0 0 10 10"><path d="M2 1l2 2-1 1.5q1 2 2.5 2.5L7 6l2 2-1.5 1.5Q3 8.5.5 2.5z" fill="#22b0e7"/></svg><span><b>Wollongong</b> - 02 4239 5817</span></li>
  </ul>

  <div class="col-title" style="left:731px">Quick links<span></span></div>
  <ul class="quick-links">
    <li>Home</li><li>Solar Cleaning</li><li>Gutter Cleaning</li><li>LumaDust</li><li>Contact us</li><li>Terms and conditions</li><li>Privacy policy</li>
  </ul>

  <a class="social" href="#" aria-label="Social profile" style="top:83px"></a>
  <a class="social" href="#" aria-label="Social profile" style="top:121px"></a>
  <a class="social" href="#" aria-label="Social profile" style="top:159px"></a>
  <a class="social" href="#" aria-label="Social profile" style="top:196px"></a>

  <p class="footer-bottom" style="left:200px">© 2025 <b>Brightleaf.</b> All Right Reserved</p>
  <p class="footer-bottom" style="left:469px"><b>ABN:</b> 48093716552</p>
  <svg class="abs" style="left:1086px;top:314px;width:14px;height:14px" viewBox="0 0 14 14" aria-label="Back to top"><path d="M7 1l5 12-5-3-5 3z" fill="#22b0e7"/></svg>
</footer>

</body>
</html>
```